Brevard Trade Partners - we are Asian sourcing agents

We are sourcing agents based in the USA and we act as sourcing agents for clients in throughout the world. We focus primarily on custom sewn goods. So basically companies who do not have the in-house expertise to do it themselves, come to us and have us find suitable factories in Asia to do the production. We are middlemen. We find the factories...quote the project...manage the quality control and then deliver the goods directly to our customer's door. We pride ourselves in making the communication very easy and precise.

Current page is www.brevardtradepartners.com

I am not happy w/ the overall look. The spacing...the photos, the fonts...the design elements...the pictures. I want a cool, crisp design that conveys professionalism and clearly depicts/explains what we do.

Requirements
Must have
• use my logo....I like it...it was designed by someone on this website.
Nice to have
• a video/animation of the entire process would be wonderful. Showing initial contact with our office in the USA...then to my correspondence with my offices in Taiwan and in Hong Kong...and then back and fort w/ the customer.....and then between my people in Hong Kong/Taiwan with the local factories......and then a quote is generated and sent to my client......to samples being made and sent for approval.....to a PO being generated......to final samples being sent.....to the order being shipped and delivered to the clients warehouse. I was thinking of an animation showing arrows and text showing the back and forth communication and explaining how the process flows.

```html
<!DOCTYPE html>
<html lang="en">
<head>
<meta charset="utf-8">
<title>Brevard Trade Partners</title>
<link href="https://fonts.googleapis.com/css2?family=Open+Sans:ital,wght@0,400;0,600;0,700;1,700&display=swap" rel="stylesheet">
<style>
:root{
  --green:#6a8f1e;
  --green-btn:#6b8a2a;
  --navy:#1d2f6b;
  --blue-btn:#1f3f8f;
  --text:#555;
  --text-dark:#333;
  --grey-band:#ebebeb;
  --panel:#f4f4f4;
  --footer:#3b3b3b;
  --footer-bottom:#2e2e2e;
  --footer-text:#d8d8d8;
}
*{box-sizing:border-box;margin:0;padding:0}
html,body{width:682px;height:1200px;overflow:hidden}
body{font-family:"Open Sans",Arial,sans-serif;color:var(--text);background:#fff;position:relative}
.abs{position:absolute}
h2{font-size:10px;font-weight:600;color:var(--green);text-transform:uppercase;letter-spacing:.1px}
p{font-size:6.2px;line-height:14.5px}
ul{list-style:none}

.site-header{left:0;top:0;width:682px;height:57px;border-top:2px solid var(--green);background:#fff}
.brand{left:57px;top:20px;font-size:10px;font-weight:700;color:var(--navy);letter-spacing:.3px;display:flex;align-items:center;gap:5px}
.brand-square{width:8px;height:8px;background:var(--green)}
.main-nav{top:23px;font-size:6.6px;text-transform:uppercase;color:#555}
.main-nav.current{color:var(--navy);font-weight:700}

.hero{left:0;top:57px;width:682px;height:257px;background:linear-gradient(180deg,#8e8a6a 0%,#a59c78 45%,#6f6142 65%,#4d5a55 85%,#3b4844 100%)}
.slider-arrow{top:183px;width:27px;height:27px;border:2px solid rgba(255,255,255,.55);border-radius:50%}

.welcome h2{left:0;top:330px;width:682px;text-align:center}
.welcome p{left:85px;top:347px;width:512px;text-align:center}

.band-grey{left:0;top:407px;width:682px;height:213px;background:var(--grey-band)}
.sourcing h2{left:56px;top:419px}
.bullets li{font-size:6.4px;line-height:13.7px;position:relative;padding-left:11px}
.bullets li::before{content:"";position:absolute;left:1px;top:5px;width:3.5px;height:3.5px;background:var(--text);transform:rotate(45deg)}
.sourcing .intro{left:57px;top:503px;width:330px;font-family:Arial,sans-serif;font-size:5.6px;line-height:9px;color:#555}
.sourcing .intro span{display:block;margin-bottom:10px}
.btn{display:block;font-size:6.6px;text-transform:uppercase;color:#fff;text-align:center}
.btn-read{left:56px;top:582px;width:47px;height:19px;line-height:19px;background:var(--blue-btn)}

.know h2{left:412px;top:420px}
.know-panel{left:407px;top:453px;width:220px;height:120px;background:var(--panel)}
.know-panel ul{padding:12px 0 0 8px}
.know-panel li{font-size:6.2px;line-height:16.6px;position:relative;padding-left:12px}
.know-panel li::before{content:"";position:absolute;left:1px;top:7px;width:3.5px;height:3.5px;background:var(--green);transform:rotate(45deg)}
.panel-tail{left:572px;top:573px;width:0;height:0;border-left:7px solid transparent;border-right:7px solid transparent;border-top:8px solid var(--panel)}
.testimonial-name{left:480px;top:588px;width:144px;text-align:right;font-size:6.6px;font-weight:700;font-style:italic;color:var(--text-dark)}

.how h2{left:56px;top:637px}
.video{left:57px;top:662px;width:324px;height:171px;background:linear-gradient(180deg,#394a6e 0%,#4a3f45 45%,#6a4a2c 70%,#3a2a22 100%)}
.video-play{left:146px;top:70px;width:24px;height:24px}
.video-bar{left:7px;bottom:5px;width:310px;height:10px;background:rgba(20,20,20,.7)}
.video-bar svg{position:absolute;left:9px;top:2px}
.video-progress{position:absolute;left:24px;top:4px;width:226px;height:2px;background:#666}

.quote h2{left:404px;top:637px}
.quote .lead{left:404px;top:658px;width:220px;font-size:6.8px;line-height:13px;color:#666}
.quote .body{left:404px;top:693px;width:222px;font-size:5.9px;line-height:15px}
.btn-quote{left:404px;top:807px;width:81px;height:23px;line-height:22px;background:var(--green-btn);border-bottom:2px solid #4c6619}

.products-band{left:0;top:858px;width:682px;height:178px;background:var(--grey-band)}
.products h2{left:0;top:876px;width:682px;text-align:center}
.product-card{top:914px;width:117px;height:84px;background:#fff;box-shadow:0 3px 3px rgba(0,0,0,.18)}
.product-card div{position:absolute;left:10px;top:8px;width:97px;height:68px}
.product-label{top:1005px;width:117px;text-align:center;font-size:7.4px;font-weight:600;color:#777}
.carousel-arrow{top:942px;width:15px;height:15px;border-radius:50%;background:#c9c9c9}

.site-footer{left:0;top:1036px;width:682px;height:128px;background:var(--footer)}
.site-footer h3{position:absolute;font-size:8.6px;font-weight:600;color:#fff;text-transform:uppercase}
.footer-about p{position:absolute;left:56px;width:420px;font-size:5.7px;line-height:11.5px;color:var(--footer-text)}
.contact-lead{left:518px;top:1074px;font-size:6.6px;color:var(--footer-text)}
.contact li{display:flex;align-items:center;gap:6px;font-size:5.9px;color:var(--footer-text);height:17px}
.footer-bottom{left:0;top:1164px;width:682px;height:36px;background:var(--footer-bottom)}
.copyright{left:56px;top:1177px;font-size:6.4px;color:#bbb}
.social{left:525px;top:1174px;display:flex;gap:7px}
.social span{width:15px;height:15px;border-radius:50%;background:#5a5a5a;display:block}
</style>
</head>
<body>

<header class="site-header abs">
  <div class="brand abs"><span class="brand-square"></span>BREVARD TRADE PARTNERS</div>
  <a class="main-nav current abs" style="left:367px">Home</a>
  <a class="main-nav abs" style="left:413px">Product Categories</a>
  <a class="main-nav abs" style="left:512px">About Us</a>
  <a class="main-nav abs" style="left:571px">Request Quote</a>
</header>

<section class="hero abs" role="img" aria-label="City skyline photograph with a bridge over a river and boats">
</section>
<span class="slider-arrow abs" style="left:10px"></span>
<span class="slider-arrow abs" style="left:643px"></span>

<section class="welcome">
  <h2 class="abs">Welcome to our company</h2>
  <p class="abs">We outsource sewing services direct from China. Our long-established and extensive network of offshore factory-partners provides our clients with access to a wide variety of contract sewing expertise from Chinese manufacturers. Clients only need to communicate with our US agents, but will have the benefits of the cost savings &amp; quality workmanship from offshore outsourcing from Asia.</p>
</section>

<div class="band-grey abs"></div>
<section class="sourcing">
  <h2 class="abs">Sourcing Solutions</h2>
  <ul class="bullets abs" style="left:56px;top:440px">
    <li>Bags</li><li>Cases</li><li>Covers</li>
  </ul>
  <ul class="bullets abs" style="left:102px;top:440px">
    <li>Gloves</li><li>Medical</li><li>Sewn Goods</li><li>Sporting Goods</li>
  </ul>
  <div class="intro abs">
    <span>We outsource sewing services direct from China.</span>
    <span>Our long-established and extensive network of offshore factory-partners provides</span>
    <span>Our clients with access to a wide variety of contract sewing expertise from Chinese manufacturers.  Clients only need to communicate with our US agents, but will have the benefits of the cost savings &amp; quality workmanship from offshore outsourcing from Asia.</span>
  </div>
  <a class="btn btn-read abs">Read More</a>
</section>

<section class="know">
  <h2 class="abs">What you need to know</h2>
  <div class="know-panel abs">
    <ul>
      <li>Contract Sewing in China</li>
      <li>What is the Process?</li>
      <li>What the Minimum Order?</li>
      <li>Contract Outsourcing FAQ</li>
      <li>Outsourcing Case Study</li>
      <li>Custom Industrial Sewing in China</li>
    </ul>
  </div>
  <span class="panel-tail abs"></span>
  <div class="testimonial-name abs">Daniel R. Whitcombe</div>
</section>

<section class="how">
  <h2 class="abs">How it works</h2>
  <div class="video abs" role="img" aria-label="Video still of a lit avenue at dusk with traffic and a monument">
    <svg class="video-play abs" viewBox="0 0 24 24"><path d="M7 4 L20 12 L7 20 Z" fill="rgba(255,255,255,.55)"/></svg>
    <div class="video-bar abs">
      <svg width="7" height="7" viewBox="0 0 7 7"><path d="M1 0 L7 3.5 L1 7 Z" fill="#fff"/></svg>
      <span class="video-progress"></span>
    </div>
  </div>
</section>

<section class="quote">
  <h2 class="abs">Request a quote</h2>
  <p class="lead abs">Please contact us for immediate consultation regarding your outsourcing project.</p>
  <p class="body abs">Because we act as agents for dozens of clients, we can most often get the best pricing because of our combined group buying power. We are also wise to the many pitfalls that can arise when an inexperienced buyer with no local representation tries to deal directly with an Asian factory. Don't go at it alone – trust Brevard Trade Partners for your outsourced needs. You'll get the best pricing, better service and most of all, peace of mind.</p>
  <a class="btn btn-quote abs">Request Quote</a>
</section>

<div class="products-band abs"></div>
<section class="products">
  <h2 class="abs">Product Categories</h2>
  <span class="carousel-arrow abs" style="left:19px"></span>
  <span class="carousel-arrow abs" style="left:648px"></span>
  <div class="product-card abs" style="left:57px"><div role="img" aria-label="Black and grey messenger bag with red stripe" style="background:radial-gradient(ellipse at center,#3a3a3a 0%,#6a6a6a 45%,#fff 75%)"></div></div>
  <div class="product-card abs" style="left:205px"><div role="img" aria-label="Pair of black and white winter gloves" style="background:radial-gradient(ellipse at center,#cfcfcf 0%,#555 45%,#fff 75%)"></div></div>
  <div class="product-card abs" style="left:354px"><div role="img" aria-label="Navy motorcycle cover" style="background:radial-gradient(ellipse at center,#2a3470 0%,#7a80a8 45%,#fff 75%)"></div></div>
  <div class="product-card abs" style="left:506px"><div role="img" aria-label="Row of colourful phone cases" style="background:linear-gradient(90deg,#fff 5%,#333 15%,#3b4fb0 30%,#7a3aa0 45%,#c03070 60%,#d04040 75%,#d08a30 88%,#fff 95%)"></div></div>
  <div class="product-label abs" style="left:57px">BAGS</div>
  <div class="product-label abs" style="left:205px">BAGS</div>
  <div class="product-label abs" style="left:354px">BAGS</div>
  <div class="product-label abs" style="left:506px">BAGS</div>
</section>

<footer class="site-footer abs">
  <div class="footer-about">
    <h3 style="left:56px;top:22px">About Us</h3>
    <p style="top:40px">At vero eos et accusamus et iusto odio dignissimos ducimus qui blanditiis praesentium voluptatum deleniti atque corrupti quos dolores et quas molestias excepturi sint occaecati cupiditate non provident, similique sunt in culpa qui officia deserunt mollitia animi, id est laborum et dolorum fuga. Et harum quidem rerum facilis est et expedita distinctio.</p>
    <p style="top:87px">&nbsp;Nam libero tempore, cum soluta nobis est eligendi optio cumque nihil impedit quo minus id quod maxime placeat facere possimus, omnis voluptas assumenda est, omnis dolor repellendus. Temporibus autem quibusdam et aut officiis debitis aut rerum necessitatibus saepe eveniet ut et.</p>
  </div>
  <h3 style="left:518px;top:22px">Get in touch</h3>
</footer>
<div class="contact-lead abs">Job inquiries? Want to say hi?</div>
<ul class="contact abs" style="left:518px;top:1088px">
  <li><svg width="6" height="8" viewBox="0 0 6 8"><rect x=".5" y=".5" width="5" height="7" rx="1" fill="none" stroke="#4f8fd8"/></svg>(555)-014-2273</li>
  <li><svg width="8" height="6" viewBox="0 0 8 6"><rect x=".5" y=".5" width="7" height="5" fill="none" stroke="#4f8fd8"/><path d="M.5 .5 L4 3.5 L7.5 .5" fill="none" stroke="#4f8fd8"/></svg>info@brevardtradepartners.com</li>
  <li style="font-size:5.2px"><svg width="6" height="8" viewBox="0 0 6 8"><path d="M3 8 C1 5 0 4 0 3 A3 3 0 0 1 6 3 C6 4 5 5 3 8Z" fill="#4f8fd8"/><circle cx="3" cy="3" r="1" fill="#3b3b3b"/></svg>At vero eos et accusamus et iusto</li>
</ul>

<div class="footer-bottom abs"></div>
<div class="copyright abs">© Brevard Trade Partners, LLC. | USA - Hong Kong - Taipei</div>
<div class="social abs"><span></span><span></span><span></span><span></span><span></span></div>

</body>
</html>
```